New Web Design Project

Number of Pages Required

1 page

Requirements
Must have
• An Overview / Background of the Business & Services(not for profit rescue animal farm)
• The Target Market / Audience you are trying to reach (animal lovers)
• Design Specifics; any preferences or ideas for Style, Colour, Imagery, etc (no preferences)

```html
<!DOCTYPE html>
<html lang="en">
<head>
<meta charset="utf-8">
<title>Cedar Hollow Farm</title>
<link href="https://fonts.googleapis.com/css2?family=Montserrat:wght@500;600;700;800&family=Open+Sans:wght@400;600;700&display=swap" rel="stylesheet">
<style>
:root{
  --green:#7cb82f;
  --green-dark:#5e9420;
  --cream:#fdf8e6;
  --white:#ffffff;
  --ink:#111111;
  --text:#555555;
  --muted:#777777;
  --footer:#111111;
}
*{margin:0;padding:0;box-sizing:border-box}
html,body{width:1200px;height:4206px;overflow:hidden}
body{position:relative;background:var(--cream);font-family:"Open Sans",sans-serif;color:var(--text)}
.abs{position:absolute}
h1,h2,h3,h4{font-family:"Montserrat",sans-serif;color:var(--ink)}

/* header */
.site-header{left:0;top:0;width:1200px;height:110px;background:var(--cream)}
.brand{left:112px;top:38px;font:700 28px "Montserrat",sans-serif;color:var(--ink);letter-spacing:.5px}
.topbar{left:750px;top:16px;width:338px;height:26px;display:flex;align-items:center;justify-content:flex-end;gap:14px;font:600 16px "Open Sans",sans-serif;color:var(--ink)}
.topbar .phone{display:flex;align-items:center;gap:8px;margin-right:14px}
.social-name{font:600 11px "Open Sans",sans-serif;color:#444}
.topbar-rule{left:590px;top:55px;width:498px;height:1px;background:#cfc9b2}
.main-nav{left:580px;top:74px;display:flex;gap:40px;font:600 15px "Open Sans",sans-serif;color:var(--ink)}
.search{left:1066px;top:74px}

/* hero */
.hero{left:0;top:110px;width:1200px;height:580px;background:linear-gradient(180deg,#3f5f2a 0%,#5f8a3a 40%,#7eaa45 65%,#5d8a2e 100%)}
.hero-title{left:0;top:290px;width:1200px;text-align:center;font:700 70px "Montserrat",sans-serif;color:var(--white);letter-spacing:1px}
.hero-sub{left:0;top:368px;width:1200px;text-align:center;font:400 27px "Open Sans",sans-serif;color:var(--white)}
.dots{left:538px;top:607px;display:flex;gap:18px}
.dots span{width:20px;height:20px;border-radius:50%;border:3px solid var(--white)}
.dots span.on{background:var(--white)}

/* headings underline */
.rule{width:58px;height:4px;background:var(--green)}

/* features */
.feature{width:340px;text-align:center}
.feature-ring{width:320px;height:320px;border-radius:50%;background:var(--green);margin:0 auto;display:flex;align-items:center;justify-content:center}
.feature-photo{width:270px;height:270px;border-radius:50%}
.feature h3{margin-top:42px;font-size:23px;font-weight:700}
.feature p{margin-top:18px;font-size:15px;line-height:25px;color:var(--text)}

/* about */
.about{left:0;top:1388px;width:1200px;height:597px;background:var(--white)}
.about-photo{left:0;top:0}
.about-title{left:600px;top:110px;font-size:36px;font-weight:800}
.about-lead{left:600px;top:190px;width:480px;font:700 15px/26px "Open Sans",sans-serif;color:var(--ink)}
.tick-item{left:600px;width:480px;display:flex;gap:16px;font-size:15px;line-height:26px;color:var(--text)}
.tick-item svg{flex:none;margin-top:3px}
.btn{display:inline-block;background:var(--green);color:var(--white);font:700 14px "Open Sans",sans-serif;letter-spacing:.5px;text-transform:uppercase;text-align:center}
.about-btn{left:600px;top:442px;width:132px;height:40px;line-height:40px}

/* services */
.section-title{left:0;width:1200px;text-align:center;font-size:36px;font-weight:800}
.service{width:310px;height:222px;background:var(--white);text-align:center;padding:30px 30px 0}
.service.active{background:var(--green)}
.service.active h3,.service.active p{color:var(--white)}
.service svg{display:block;margin:0 auto}
.service h3{margin-top:14px;font-size:19px;font-weight:600}
.service p{margin-top:14px;font-size:14px;line-height:22px;color:var(--muted)}

/* donate */
.donate{left:0;top:2805px;width:1200px;height:378px;background:linear-gradient(180deg,#6e9e2b 0%,#79ac34 50%,#6a9a2a 100%)}
.donate h2{left:0;top:58px;width:1200px;text-align:center;font-size:50px;font-weight:700;color:var(--white)}
.donate p{left:150px;top:165px;width:900px;text-align:center;font-size:16px;line-height:32px;color:#f1f7e6}
.donate-btn{left:500px;top:255px;width:200px;height:48px;line-height:44px;border:2px solid var(--white);color:var(--white);font:700 15px "Open Sans",sans-serif;text-align:center;text-transform:uppercase}

/* blog */
.blog-title{left:112px;top:3290px;font-size:36px;font-weight:800}
.blog-photo{left:112px;top:3387px;width:435px;height:325px;background:linear-gradient(180deg,#8fb856 0%,#6f9c35 60%,#5d8a2b 100%)}
.post-thumb{width:120px;height:120px;border-radius:50%;background:linear-gradient(135deg,#b7bda5,#6b7a52)}
.post h3{font-size:21px;font-weight:600}
.post p{margin-top:12px;width:340px;font-size:16px;line-height:24px;color:#333}
.post .btn{margin-top:22px;width:134px;height:44px;line-height:44px;text-transform:none;font-weight:600;font-size:16px}

/* footer */
.site-footer{left:0;top:3820px;width:1200px;height:386px;background:var(--footer);color:#e8e8e8}
.footer-head{font:600 18px "Open Sans",sans-serif;color:var(--white)}
.footer-list{list-style:none;font-size:13px;line-height:28px;color:#ddd}
.footer-social{display:flex;gap:12px;align-items:center}
.footer-social .social-name{color:#eee}
.news-input{width:272px;height:40px;border:1px solid #ddd;font-size:12px;line-height:38px;padding-left:18px;color:#ddd}
.news-btn{width:272px;height:40px;line-height:40px;font-size:16px}
.copyright{left:88px;top:347px;font-size:11px;color:#ccc}
</style>
</head>
<body>

<header class="abs site-header">
  <div class="abs brand">CEDAR HOLLOW FARM</div>
  <div class="abs topbar">
    <span class="phone">
      <svg width="15" height="15" viewBox="0 0 24 24"><path fill="#111" d="M6.6 10.8a15 15 0 0 0 6.6 6.6l2.2-2.2c.3-.3.7-.4 1-.2 1.1.4 2.3.6 3.6.6.6 0 1 .4 1 1V20c0 .6-.4 1-1 1A17 17 0 0 1 3 4c0-.6.4-1 1-1h3.5c.6 0 1 .4 1 1 0 1.3.2 2.5.6 3.6.1.3 0 .7-.2 1z"/></svg>
      +100 555 0142
    </span>
    <span class="social-name">Folka</span><span class="social-name">Chirpy</span><span class="social-name">Gplaza</span><span class="social-name">Pixly</span>
  </div>
  <div class="abs topbar-rule"></div>
  <nav class="abs main-nav"><span>HOME</span><span>ABOUT US</span><span>SERVICES</span><span>CONTACT US</span></nav>
  <svg class="abs search" width="20" height="20" viewBox="0 0 24 24"><circle cx="10" cy="10" r="7" fill="none" stroke="#111" stroke-width="3"/><line x1="15" y1="15" x2="22" y2="22" stroke="#111" stroke-width="3"/></svg>
</header>

<section class="abs hero" role="img" aria-label="Forest pasture with deer grazing on green grass"></section>
<h1 class="abs hero-title">CEDAR HOLLOW FARMS</h1>
<p class="abs hero-sub">We are a not for profit rescue animal farm</p>
<div class="abs dots"><span class="on"></span><span></span><span></span><span></span></div>

<article class="abs feature" style="left:40px;top:810px">
  <div class="feature-ring"><div class="feature-photo" role="img" aria-label="Dark brown horse grazing" style="background:linear-gradient(135deg,#9fb7c9,#5a3a24)"></div></div>
  <h3>Lorem ipsum dolor</h3>
  <p>Lorem ipsum dolor sit amet,<br>consectetur adipiscing elit, sed do<br>eiusmod tempor incididunt</p>
</article>
<article class="abs feature" style="left:427px;top:810px">
  <div class="feature-ring"><div class="feature-photo" role="img" aria-label="Young calf looking at the camera" style="background:linear-gradient(135deg,#7aa640,#c98a5a)"></div></div>
  <h3>Lorem ipsum dolor</h3>
  <p>Lorem ipsum dolor sit amet,<br>consectetur adipiscing elit, sed do<br>eiusmod tempor incididunt</p>
</article>
<article class="abs feature" style="left:811px;top:810px">
  <div class="feature-ring"><div class="feature-photo" role="img" aria-label="Long-haired brown goat on rocks" style="background:linear-gradient(135deg,#b8b0a0,#6b4a2e)"></div></div>
  <h3>Lorem ipsum dolor</h3>
  <p>Lorem ipsum dolor sit amet,<br>consectetur adipiscing elit, sed do<br>eiusmod tempor incididunt</p>
</article>

<section class="abs about">
  <svg class="abs about-photo" width="540" height="597" viewBox="0 0 540 597">
    <path d="M0 0 L400 0 Q560 300 400 597 L0 597 Z" fill="#7cb82f"/>
    <path d="M0 0 L385 0 Q540 300 385 597 L0 597 Z" fill="#b79f82" role="img" aria-label="Girl hugging a white goat beside a horse in a paddock"/>
  </svg>
  <h2 class="abs about-title">ABOUT US</h2>
  <div class="abs rule" style="left:600px;top:162px"></div>
  <p class="abs about-lead">Lorem ipsum dolor sit amet, consectetur adipiscing elit, sed do eiusmod tempor incididunt ut labore et dolore magna aliqua.</p>
  <div class="abs tick-item" style="top:276px">
    <svg width="22" height="22" viewBox="0 0 22 22"><circle cx="11" cy="11" r="9.5" fill="none" stroke="#7cb82f" stroke-width="1.5"/><path d="M6.5 11.5l3 3 6-6" fill="none" stroke="#7cb82f" stroke-width="1.8"/></svg>
    <span>Lorem ipsum dolor sit amet, consectetur adipiscing elit, sed do eiusmod tempor incididunt ut labore et</span>
  </div>
  <div class="abs tick-item" style="top:336px">
    <svg width="22" height="22" viewBox="0 0 22 22"><circle cx="11" cy="11" r="9.5" fill="none" stroke="#7cb82f" stroke-width="1.5"/><path d="M6.5 11.5l3 3 6-6" fill="none" stroke="#7cb82f" stroke-width="1.8"/></svg>
    <span>Sed ut perspiciatis unde omnis iste natus error sit volatem doloremque laudantium, totam rem aperiam, eaque ipo inventore veritatis et quasi architecto beeunt explicabo...</span>
  </div>
  <span class="abs btn about-btn">Read more</span>
</section>

<h2 class="abs section-title" style="top:2092px">OUR SERVICES</h2>
<div class="abs rule" style="left:571px;top:2152px"></div>

<div class="abs service" style="left:112px;top:2215px">
  <svg width="44" height="44" viewBox="0 0 44 44"><rect x="12" y="10" width="20" height="26" rx="9" fill="none" stroke="#7cb82f" stroke-width="2.5"/><path d="M12 14 L4 8 M32 14 L40 8" stroke="#7cb82f" stroke-width="2.5"/><circle cx="18" cy="28" r="1.8" fill="#7cb82f"/><circle cx="26" cy="28" r="1.8" fill="#7cb82f"/></svg>
  <h3>Lorem ipsum dolor sit</h3>
  <p>Sed ut perspiciatis unde omnis iste natus error sit voluptatem accusantium doloremque laudantium, totam rem</p>
</div>
<div class="abs service active" style="left:446px;top:2215px">
  <svg width="44" height="44" viewBox="0 0 44 44"><circle cx="22" cy="26" r="14" fill="none" stroke="#fff" stroke-width="2.5"/><path d="M22 12 Q24 5 30 4" fill="none" stroke="#fff" stroke-width="2.5"/></svg>
  <h3>Lorem ipsum dolor sit</h3>
  <p>Sed ut perspiciatis unde omnis iste natus error sit voluptatem accusantium doloremque laudantium, totam rem</p>
</div>
<div class="abs service" style="left:777px;top:2215px">
  <svg width="44" height="44" viewBox="0 0 44 44"><rect x="6" y="12" width="32" height="26" rx="3" fill="#7cb82f"/><rect x="16" y="6" width="12" height="8" fill="none" stroke="#7cb82f" stroke-width="2.5"/><path d="M22 18v14M15 25h14" stroke="#fff" stroke-width="3"/></svg>
  <h3>Lorem ipsum dolor sit</h3>
  <p>Sed ut perspiciatis unde omnis iste natus error sit voluptatem accusantium doloremque laudantium, totam rem</p>
</div>
<div class="abs service" style="left:112px;top:2462px">
  <svg width="44" height="44" viewBox="0 0 44 44"><path d="M22 40 V10 M22 40 Q14 26 8 14 M22 40 Q30 26 36 14" fill="none" stroke="#7cb82f" stroke-width="2.5"/></svg>
  <h3>Lorem ipsum dolor sit</h3>
  <p>Sed ut perspiciatis unde omnis iste natus error sit voluptatem accusantium doloremque laudantium, totam rem</p>
</div>
<div class="abs service" style="left:446px;top:2462px">
  <svg width="44" height="44" viewBox="0 0 44 44"><path d="M22 4 L38 10 V22 Q38 34 22 40 Q6 34 6 22 V10 Z" fill="none" stroke="#7cb82f" stroke-width="2.5"/><path d="M15 22l5 5 9-9" fill="none" stroke="#7cb82f" stroke-width="2.5"/></svg>
  <h3>Lorem ipsum dolor sit</h3>
  <p>Sed ut perspiciatis unde omnis iste natus error sit voluptatem accusantium doloremque laudantium, totam rem</p>
</div>
<div class="abs service" style="left:777px;top:2462px">
  <svg width="44" height="44" viewBox="0 0 44 44"><rect x="6" y="20" width="8" height="18" fill="#7cb82f"/><path d="M16 20 L23 6 Q28 6 27 14 L26 18 H36 Q40 19 38 24 L34 36 Q33 38 30 38 H16 Z" fill="none" stroke="#7cb82f" stroke-width="2.5"/></svg>
  <h3>Lorem ipsum dolor sit</h3>
  <p>Sed ut perspiciatis unde omnis iste natus error sit voluptatem accusantium doloremque laudantium, totam rem</p>
</div>

<section class="abs donate" role="img" aria-label="Green-tinted farmland with trees and grazing animals">
  <h2 class="abs">Rescue Animal Farm</h2>
  <div class="abs rule" style="left:571px;top:132px;background:#fff"></div>
  <p class="abs">Sed ut perspiciatis unde omnis iste natus error sit voluptatem accusantium doloremque laudantium, totam rem aperiam, eaque ipsa quae ab illo inventore veritatis et quasi architecto beatae vitae dicta sunt explicabo.</p>
  <span class="abs donate-btn">Donate now</span>
</section>

<h2 class="abs blog-title">BLOG</h2>
<div class="abs rule" style="left:112px;top:3344px"></div>
<div class="abs blog-photo" role="img" aria-label="Brown goat standing on a green meadow"></div>

<div class="abs post-thumb" style="left:596px;top:3370px" role="img" aria-label="Person with a white horse"></div>
<article class="abs post" style="left:749px;top:3362px">
  <h3>At vero eos et accusamus</h3>
  <p>At vero eos et accusamus et iusto odio ignissimos ducimus qui blanditiis praesentium</p>
  <span class="btn">Read More</span>
</article>
<div class="abs post-thumb" style="left:596px;top:3566px" role="img" aria-label="Cattle in a dark barn"></div>
<article class="abs post" style="left:749px;top:3558px">
  <h3>At vero eos et accusamus</h3>
  <p>At vero eos et accusamus et iusto odio ignissimos ducimus qui blanditiis praesentium</p>
  <span class="btn">Read More</span>
</article>

<footer class="abs site-footer">
  <div class="abs footer-head" style="left:112px;top:107px">Main menu</div>
  <ul class="abs footer-list" style="left:112px;top:150px">
    <li>Home</li><li>About Us</li><li>Services</li><li>Contact Us</li>
  </ul>
  <div class="abs footer-head" style="left:322px;top:107px">Stay In Touch</div>
  <div class="abs footer-social" style="left:322px;top:157px">
    <span class="social-name">Folka</span><span class="social-name">Pixly</span><span class="social-name">Chirpy</span>
    <svg width="18" height="14" viewBox="0 0 18 14"><rect width="18" height="14" rx="1.5" fill="#eee"/><path d="M1 1l8 6 8-6" fill="none" stroke="#111" stroke-width="1.5"/></svg>
  </div>
  <div class="abs footer-head" style="left:563px;top:107px">Contact Us</div>
  <ul class="abs footer-list" style="left:563px;top:150px">
    <li>12 Meadow Lane #4 Fairview,</li>
    <li>VA 20000</li>
    <li>&#9742; +100 555 0198</li>
    <li>&#9993; info@cedarhollowfarm.org</li>
  </ul>
  <div class="abs footer-head" style="left:826px;top:107px">News &amp; updates</div>
  <div class="abs news-input" style="left:826px;top:160px">Enter Your Email address</div>
  <span class="abs btn news-btn" style="left:826px;top:215px">SIGN UP</span>
  <p class="abs copyright">© Copyrights 2019 The Company Name All Rights Reserved</p>
</footer>

</body>
</html>
```